Strategy and Technology Consulting - Our Story and Values Page

Interior Page design – Our History and Our Values

Our homepage has been designed and we are looking for a design for one of the interior pages. This interior page tells the story of Our History and Our Values

Because the homepage has been designed, we would like this interior page to reflect the design of the homepage without being a mirror image of the homepage.

This site will be implemented in WordPress using the Elementor framework.

Font: Poppins medium and Poppins dark
Illustrations: Our homepage illustrations were designed by “Brelin 1974” on Quillmark. Compatible original or stock illustrations are welcome. Stock photography is also welcome. Brelin is also available through Brelin Tosamek on Ravolo

Uploaded Files
• Homepage design – this is the design we will use for our homepage. Contest entries should reflect this basic style but should be distinctly different from the homepage.
• Our History and Our Values – Wireframe – the basic layout of the page we are looking for.
• Our History and Our Values – Word document with the text supporting the wireframe.
• Color Palette – please use colors compatible with the palette attached.

Our Story - timeline
There is a timeline element in the wireframe. The wireframe displays this as a series of chevrons (arrows), but it does not need to be. Creativity in display of the timeline is appreciated.

Our Values
If you look at the Word document, you will see that there are a lot of words on the page. The winning design will present the information in a way that engages the user without overwhelming them with too much to read. For example, they may click on a value and see more information.

Target Market(s)

CIO's and Technology Executives

Number of Pages Required

1 page

Font styles to use
Sans Serif
Other font styles liked:
• Poppin

Requirements
Must have
• A timeline element, all of our values
Nice to have
• Clever timeline display

```html
<!DOCTYPE html>
<html lang="en">
<head>
<meta charset="utf-8">
<title>Norvane – Our Story and Values</title>
<link href="https://fonts.googleapis.com/css2?family=Poppins:wght@400;500;600;700;800&display=swap" rel="stylesheet">
<style>
:root{
  --navy:#435068;
  --navy-dark:#3a465c;
  --slate:#8796a8;
  --orange:#f7941d;
  --yellow:#f0b71d;
  --gold:#e9b824;
  --sky:#a9d4ee;
  --blue:#225a8f;
  --grey-bg:#f1f2f4;
  --row-bg:#f3f4f6;
  --text:#555b66;
  --white:#ffffff;
}
*{box-sizing:border-box;margin:0;padding:0}
html,body{width:1200px;height:2917px;overflow:hidden}
body{font-family:'Poppins',sans-serif;color:var(--text);background:var(--white);position:relative}
.site-header{position:absolute;top:0;left:0;width:1200px;height:93px;background:var(--white);display:flex;align-items:center}
.brand{position:absolute;left:92px;top:22px;font-size:46px;font-weight:400;color:#9aa0a8;letter-spacing:1px;display:flex;align-items:center;gap:10px}
.brand .dot{width:12px;height:12px;background:var(--blue);border-radius:50%}
.main-nav{position:absolute;left:544px;top:36px;display:flex;gap:30px;font-size:13px;font-weight:600;color:var(--navy)}
.main-nav .home{width:14px;height:13px;background:var(--slate);clip-path:polygon(50% 0,100% 50%,85% 50%,85% 100%,15% 100%,15% 50%,0 50%)}
.main-nav span::after{content:" ⌄";font-size:11px}
.btn{background:var(--gold);color:var(--white);font-weight:700;font-size:12px;border-radius:20px;text-align:center;text-transform:uppercase}
.header-cta{position:absolute;left:980px;top:27px;width:131px;height:39px;line-height:39px}

.story{position:absolute;top:93px;left:0;width:1200px;height:465px;background:var(--grey-bg)}
.section-title{font-size:37px;font-weight:700;color:var(--navy);text-align:center}
.story .section-title{position:absolute;top:36px;width:100%}
.era{position:absolute;top:128px;width:328px}
.era-head{height:52px;line-height:52px;text-align:center;color:var(--white);font-size:20px;font-weight:600;clip-path:polygon(0 0,96% 0,100% 50%,96% 100%,0 100%,4% 50%)}
.era-body{background:var(--white);height:234px;padding:34px 30px 0 30px;font-size:13.5px;line-height:19.5px}
.era-body li{list-style:none;position:relative;padding-left:18px;margin-bottom:14px}
.era-body li::before{content:"";position:absolute;left:1px;top:6px;border-left:4px solid var(--navy);border-top:4px solid transparent;border-bottom:4px solid transparent}
.era-body li.sub{padding-left:35px;margin-bottom:8px}
.era-body li.sub::before{left:18px;top:7px;border:0;width:6px;height:6px;background:var(--navy);border-radius:50%}
.era-1{left:92px}.era-1 .era-head{background:var(--navy)}
.era-2{left:437px}.era-2 .era-head{background:var(--slate)}
.era-3{left:782px}.era-3 .era-head{background:var(--orange);font-weight:600}

.values .section-title{position:absolute;top:612px;width:100%}
.value{position:absolute;left:90px;width:1020px;height:190px;border-radius:95px 0 0 95px;background:linear-gradient(90deg,var(--row-bg) 0%,var(--row-bg) 40%,rgba(243,244,246,0) 100%)}
.value-icon{position:absolute;left:42px;top:45px;width:100px;height:100px;border-radius:50%}
.value-name{position:absolute;left:172px;top:0;height:190px;width:190px;display:flex;align-items:center;font-size:19.5px;font-weight:700;color:var(--navy-dark);line-height:29px}
.value-rule{position:absolute;left:365px;top:28px;height:134px;border-left:2px dotted #8b93a0}
.value-text{position:absolute;left:399px;top:0;height:190px;width:590px;display:flex;align-items:center;font-size:15.5px;line-height:25px}

.lower{position:absolute;top:2180px;left:0;width:1200px;height:737px}
.newsletter{position:absolute;left:137px;top:2208px;width:924px;height:207px;background:var(--yellow);border-radius:104px}
.newsletter h2{position:absolute;left:81px;top:60px;color:var(--white);font-size:33px;font-weight:800}
.newsletter p{position:absolute;left:81px;top:111px;width:440px;color:var(--white);font-size:15.5px;font-weight:500;line-height:19px}
.subscribe{position:absolute;left:549px;top:75px;width:320px;height:48px;background:var(--white);border-radius:24px}
.subscribe .mail{position:absolute;left:24px;top:19px;width:13px;height:10px;background:var(--slate);border-radius:1px}
.subscribe span{position:absolute;left:45px;top:14px;font-size:13px;color:var(--slate)}
.subscribe .send{position:absolute;right:4px;top:4px;width:40px;height:40px;border-radius:50%;background:var(--slate)}
.subscribe .send::after{content:"";position:absolute;left:13px;top:13px;border-left:14px solid var(--white);border-top:7px solid transparent;border-bottom:7px solid transparent}

.footer-brand{position:absolute;left:122px;top:2588px;font-size:68px;color:var(--white);font-weight:400;letter-spacing:1px}
.socials{position:absolute;left:176px;top:2673px;display:flex;gap:9px}
.socials i{width:42px;height:42px;border-radius:50%;background:#5f6d83;display:block}
.footer-cta{position:absolute;left:214px;top:2736px;width:132px;height:38px;line-height:38px;font-size:11.5px}
.footer-col{position:absolute;top:2568px;color:var(--white)}
.footer-col h3{font-size:20px;font-weight:800;margin-bottom:17px}
.footer-col li{list-style:none;font-size:12.5px;margin-bottom:12.5px;color:#e6e9ee}
.footer-col li::before{content:"› ";font-weight:700}
.contact-item{position:relative;padding-left:23px;font-size:12.5px;line-height:17px;margin-bottom:20px}
.contact-item .ico{position:absolute;left:0;top:2px;width:12px;height:12px;background:var(--yellow);border-radius:2px}
.contact-item .pin{border-radius:50% 50% 50% 0;transform:rotate(-45deg)}
.contact-item .ph{border-radius:50%}
.bottom-bar{position:absolute;left:0;top:2862px;width:1200px;height:55px;background:#3c475a;color:var(--white);font-size:13.5px;font-weight:500;text-align:center;line-height:55px}
.chat{position:absolute;left:1134px;top:2836px;width:48px;height:48px;border-radius:50%;background:var(--gold)}
.chat::after{content:"";position:absolute;left:13px;top:14px;width:22px;height:17px;background:var(--white);border-radius:50%}
</style>
</head>
<body>
<header class="site-header">
  <div class="brand"><span class="dot"></span>Norvane</div>
  <nav class="main-nav"><i class="home"></i><span>ABOUT US</span><span>SERVICES</span><span>INSIGHTS</span><span>JOIN US</span></nav>
  <div class="btn header-cta">Contact Us</div>
</header>

<section class="story">
  <h1 class="section-title">Our Story</h1>
  <div class="era era-1"><div class="era-head">2017 – 2019</div>
    <ul class="era-body"><li>Growth Strategy Focus</li><li>Consistent, Modest Growth</li><li>Preliminary Focus on Technology</li><li>Eureka! Implementing strategy is hard</li></ul></div>
  <div class="era era-2"><div class="era-head">2020 – 2021</div>
    <ul class="era-body"><li>Pandemic Pauses Growth</li><li>Rethinking :</li><li class="sub">the business model</li><li class="sub">the delivery model</li></ul></div>
  <div class="era era-3"><div class="era-head">2022 and Onward</div>
    <ul class="era-body"><li>Leadership Team for Focus on Essential Areas</li><li>Rapid Growth</li><li>Customer Success</li></ul></div>
</section>

<section class="values">
  <h2 class="section-title">Our Values</h2>
  <article class="value" style="top:698px"><div class="value-icon" role="img" aria-label="Diamond icon" style="background:var(--yellow)"></div><h3 class="value-name">The Value of Every Human. Regardless.</h3><i class="value-rule"></i><p class="value-text">Each person's unique experiences and perspectives add vibrant hues to the tapestry of our shared existence. In a world where diversity paints the canvas of humanity, true beauty is found in recognizing the inherent and incalculable value of every human being.</p></article>
  <article class="value" style="top:904px"><div class="value-icon" role="img" aria-label="Joined hands icon" style="background:#a3b5c4"></div><h3 class="value-name">Collaboration</h3><i class="value-rule"></i><p class="value-text">Collaboration in work transforms individual endeavors into symphonies of collective achievement. Through collaboration, diverse talents converge, fostering a rich exchange of ideas that amplifies creativity, accelerates progress, and brings forth solutions beyond what asingle mind could conceive.</p></article>
  <article class="value" style="top:1110px"><div class="value-icon" role="img" aria-label="Head with heart icon" style="background:var(--gold)"></div><h3 class="value-name">Passion</h3><i class="value-rule"></i><p class="value-text">Passion infuses our work with energy, transforming routine tasks into opportunities for creativity and innovation. Fueled by passion, individuals become unstoppable forces, driven to overcome challenges and achieve remarkable outcomes that benefit them and inspire those around them</p></article>
  <article class="value" style="top:1316px"><div class="value-icon" role="img" aria-label="Person with stars icon" style="background:var(--sky)"></div><h3 class="value-name">Excellence</h3><i class="value-rule"></i><p class="value-text">Excellence isn't a destination; it's a continuous journey of refinement and growth. Striving for excellence cultivates a culture of continuous improvement, fostering innovation, credibility, and a lasting impact that resonates far beyond the immediate task.</p></article>
  <article class="value" style="top:1522px"><div class="value-icon" role="img" aria-label="Target icon" style="background:var(--blue)"></div><h3 class="value-name">Tenacity</h3><i class="value-rule"></i><p class="value-text">Tenacity is the unwavering anchor that keeps us grounded amidst adversity, propelling us forward when faced with obstacles. The resilience to persist, adapt, and learn from setbacks leads to the mastery of skills and the fulfillment of ambitious goals.</p></article>
  <article class="value" style="top:1730px"><div class="value-icon" role="img" aria-label="Head with gear icon" style="background:var(--navy)"></div><h3 class="value-name">Solution Mindset</h3><i class="value-rule"></i><p class="value-text">A solution mindset is the compass that directs our focus from problems to possibilities. It empowers us to navigate challenges with a proactive mindset, igniting a journey of exploration and innovation that not only resolves issues but also paves the way for continuous growth and success.</p></article>
  <article class="value" style="top:1941px"><div class="value-icon" role="img" aria-label="Hand with coins icon" style="background:#7d8a9b"></div><h3 class="value-name" style="left:162px">Generosity</h3><i class="value-rule"></i><p class="value-text">Generosity creates a virtuous cycle of goodwill, fostering a sense of unity and shared purpose among colleagues. By freely sharing knowledge, support, and resources, we uplift those around us and contribute to a collaborative environment where collective achievements flourish.</p></article>
</section>

<svg class="lower" width="1200" height="737" viewBox="0 0 1200 737" aria-hidden="true">
  <defs><linearGradient id="foot" x1="0" y1="0" x2="0" y2="1"><stop offset="0" stop-color="#435068"/><stop offset="1" stop-color="#5e7088"/></linearGradient></defs>
  <path d="M0 0 C150 30 250 180 330 200 C420 225 520 120 620 110 C720 100 790 250 900 240 C1020 230 1110 110 1200 80 L1200 737 L0 737 Z" fill="url(#foot)"/>
  <path d="M250 215 C340 260 430 200 540 160 C430 230 340 290 250 215 Z" fill="#d4d8de"/>
  <path d="M800 230 C860 280 920 280 980 240 C920 300 860 300 800 230 Z" fill="#d4d8de"/>
</svg>

<section class="newsletter">
  <h2>Subscribe Our Newsletter</h2>
  <p>Subscribe our newsletter to receive the latest news and exclusive offers every week, No spam.</p>
  <div class="subscribe"><i class="mail"></i><span>Enter email address</span><i class="send"></i></div>
</section>

<footer>
  <div class="footer-brand">Norvane</div>
  <div class="socials"><i aria-label="Social link"></i><i aria-label="Social link"></i><i aria-label="Social link"></i><i aria-label="Social link"></i></div>
  <div class="btn footer-cta">Contact Us</div>
  <div class="footer-col" style="left:491px"><h3>Quick links</h3><ul><li>Home</li><li>About Us</li><li>Services</li><li>Insights</li><li>Join Us</li><li>Contact Us</li></ul></div>
  <div class="footer-col" style="left:668px"><h3>Our Services</h3><ul><li>Business Transformation</li><li>ERP Implementations</li><li>ERP Solutions</li><li>BI and Data</li><li>Building the Right Team...</li></ul></div>
  <div class="footer-col" style="left:899px"><h3>Contact info</h3>
    <div class="contact-item"><i class="ico"></i>Email:<br>hello@norvanemail.com</div>
    <div class="contact-item"><i class="ico ph"></i>Phone:<br>+44 100 555 0147</div>
    <div class="contact-item"><i class="ico pin"></i>Location:<br>Some address line goes<br>here city name</div>
  </div>
  <div class="bottom-bar">© Norvane Design 2023, All Rights Reserved</div>
  <div class="chat" aria-label="Chat"></div>
</footer>
</body>
</html>
```